eCommerce Website Design for Children's Book Service

I am looking for a 5 page eCommerce website that includes a Shopping Cart. 'Lumiva Books' is the title of the company and its logo is attached. 'Sprouting wonder in words,' is the company's motto and 'spring green' is the main color. The website needs to appeal to families. Images of books and/or maple seeds (helicopter seeds) moving are part of the graphics.
Updates

I have updated my brief and I would like my website design to include 5 pages: home, about, products (books), blog, contact. WordPress is the web format that I am most comfortable with.

Target Market(s)

Families with young children

Coding

Coded - Design and coding required

Number of Pages Required

5+ page

Requirements
Must have
• Shopping cart page; contact page, books page with spaces of photos to go, blog page; spring green color
Nice to have
• A graphic that relates to motto : "sprouting wonder in words"
• WordPress

```html
<!DOCTYPE html>
<html lang="en">
<head>
<meta charset="utf-8">
<title>Lumiva Books – Sprouting wonder in words</title>
<link href="https://fonts.googleapis.com/css2?family=Poppins:wght@400;500;600;700&family=Open+Sans:wght@400;600;700&display=swap" rel="stylesheet">
<style>
:root{
  --green:#2f9a2a;
  --green-bright:#3aa62f;
  --ink:#222;
  --text:#555;
  --white:#fff;
  --lavender:#eff1f9;
  --mint:#e6f1f4;
}
*{box-sizing:border-box;margin:0;padding:0}
html,body{width:1200px;height:3455px;overflow:hidden}
body{position:relative;background:var(--white);font-family:"Open Sans",sans-serif;color:var(--text)}
.abs{position:absolute}
/* top bar */
.topbar{left:0;top:0;width:1200px;height:35px;background:var(--green);z-index:10}
.topbar .social{left:140px;top:11px;display:flex;gap:14px}
.topbar .social span{width:13px;height:13px;border-radius:50%;background:var(--white);display:block}
.topbar .account{right:112px;top:0;height:35px;display:flex;align-items:center;gap:22px;color:var(--white);font-size:13px}
.topbar .sep{width:1px;height:16px;background:rgba(255,255,255,.7)}
/* header */
.header{left:0;top:35px;width:1200px;height:103px;background:var(--white)}
.brand-disc{left:97px;top:-4px;width:206px;height:206px;border-radius:50%;background:var(--white);z-index:5;display:flex;align-items:flex-end;justify-content:center;padding-bottom:50px}
.brand-disc .name{font-family:"Poppins",sans-serif;font-weight:600;font-size:24px;color:var(--green)}
.nav{left:527px;top:53px;display:flex;gap:24px;font-size:14px;font-weight:600;color:#444}
.search-pill{left:804px;top:86px;width:251px;height:40px;border:1.5px solid #888;border-radius:20px;display:flex;align-items:center;justify-content:center;gap:8px;font-size:14px;font-weight:600;color:#333;background:var(--white)}
/* hero */
.hero{left:0;top:138px;width:1200px;height:502px;background:radial-gradient(ellipse at 22% 55%,#e7b98a 0%,#dba477 16%,rgba(225,215,205,0) 40%),linear-gradient(180deg,rgba(122,170,90,.35) 0%,rgba(255,255,255,0) 30%),linear-gradient(90deg,#d9d3cc 0%,#e8e3de 45%,#f1eeea 100%)}
.hero-title{left:574px;top:242px;font-family:"Poppins",sans-serif;font-weight:700;font-size:58px;line-height:66px;color:var(--green-bright)}
.hero-sub{left:576px;top:400px;font-size:19px;color:#333;font-weight:600}
.signup{left:571px;top:455px;width:438px;height:55px;background:var(--white);border-radius:28px;box-shadow:0 2px 6px rgba(0,0,0,.12)}
.signup .ph{left:24px;top:16px;font-size:18px;color:#555}
.signup .btn{right:5px;top:5px;width:178px;height:45px;border-radius:23px;background:var(--green);color:var(--white);font-weight:700;font-size:17px;display:flex;align-items:center;justify-content:center}
.dots{left:573px;top:603px;display:flex;gap:6px}
.dots span{width:9px;height:9px;border-radius:50%;border:1.5px solid var(--white)}
.dots span.on{background:var(--white)}
/* welcome */
.section-title{font-family:"Poppins",sans-serif;font-weight:500;color:var(--ink);text-align:center;width:1200px;left:0}
.welcome-title{top:710px;font-size:36px}
.welcome-lead{left:270px;top:768px;width:660px;text-align:center;font-size:14.5px;line-height:25px;color:#444;font-weight:600}
.welcome-body{left:262px;top:830px;width:676px;text-align:center;font-size:12.5px;line-height:29px;color:#666}
.outline-btn{border:2px solid var(--green);border-radius:20px;color:#333;font-weight:700;display:flex;align-items:center;justify-content:center;background:var(--white)}
.about-btn{left:541px;top:946px;width:150px;height:35px;font-size:12px}
/* order */
.order-band{left:0;top:1052px;width:1200px;height:542px;background:radial-gradient(circle at 15% 30%,#dcebe0 0%,rgba(230,241,244,0) 35%),radial-gradient(circle at 85% 75%,#d9eadc 0%,rgba(230,241,244,0) 35%),var(--mint)}
.ribbon{left:447px;top:1052px;width:306px;height:108px}
.ribbon-text{left:447px;top:1070px;width:306px;text-align:center;font-family:"Poppins",sans-serif;font-size:36px;font-weight:500;color:var(--white)}
.offer-card{left:143px;top:1198px;width:912px;height:350px;background:var(--white);box-shadow:0 3px 10px rgba(0,0,0,.18)}
.offer-book{left:76px;top:58px;width:272px;height:226px;border-radius:6px;background:linear-gradient(135deg,#1e5a56 0%,#245f5a 55%,#3a3a5a 100%)}
.offer-shadow{left:88px;top:292px;width:240px;height:14px;border-radius:50%;background:#d8d8d8}
.offer-title{left:433px;top:30px;font-family:"Poppins",sans-serif;font-weight:700;font-size:35px;line-height:38px;color:var(--green-bright)}
.offer-price{left:433px;top:113px;font-family:"Poppins",sans-serif;font-weight:600;font-size:30px;color:#333}
.qty-row{left:433px;top:170px;display:flex;align-items:center;gap:14px;font-size:17px;font-weight:600;color:#555}
.qty{width:78px;height:28px;border:1.5px solid #aaa;border-radius:14px;display:flex;align-items:center;justify-content:space-around;font-size:15px;color:#333}
.buy-btn{width:116px;height:28px;border-radius:14px;background:var(--green);color:var(--white);font-size:12px;font-weight:700;display:flex;align-items:center;justify-content:center}
.offer-desc{left:433px;top:210px;width:450px;font-size:12.5px;line-height:27px;color:#555}
/* shop */
.shop-title{top:1660px;font-size:34px}
.product{width:201px;text-align:center}
.product .frame{width:201px;height:154px;border:2px solid var(--green);background:var(--white);position:relative}
.product .cover{position:absolute;left:70px;top:20px;width:60px;height:104px;border-radius:3px}
.product .cover-shadow{position:absolute;left:58px;top:125px;width:84px;height:9px;border-radius:50%;background:#e2e2e2}
.product .name{margin-top:22px;font-size:18px;line-height:27px;color:#333}
.product .price{margin-top:4px;font-size:17px;font-weight:700;color:var(--green)}
.product.active{border:2px solid var(--green);height:334px;background:var(--white)}
.product.active .frame{border:none;width:100%;height:150px}
.product.active .name{margin-top:18px}
.cart-btn{margin:12px auto 0;width:140px;height:30px;border-radius:15px;background:var(--green);color:var(--white);font-size:13px;font-weight:700;display:flex;align-items:center;justify-content:center}
.cursor{left:318px;top:2068px}
.more-btn{left:534px;top:2475px;width:132px;height:44px;font-size:16px;border-radius:22px}
/* search */
.finder{left:0;top:2593px;width:1200px;height:560px;background:var(--lavender)}
.finder-title{left:187px;top:2652px;font-family:"Poppins",sans-serif;font-weight:400;font-size:36px;color:var(--green)}
.finder-label{left:191px;font-size:19px;font-weight:700;color:#333}
.field{left:191px;width:304px;height:46px;border:1.5px solid #aaa;background:var(--white);font-size:15px;color:#444;display:flex;align-items:center;justify-content:space-between;padding:0 20px}
.search-btn{left:191px;top:3034px;width:150px;height:40px;border-radius:20px;background:var(--green);color:var(--white);font-weight:700;font-size:15px;display:flex;align-items:center;justify-content:center}
.finder-brand{left:620px;top:2870px;width:390px;text-align:center;font-family:"Poppins",sans-serif;font-weight:600;font-size:64px;line-height:72px;color:var(--green)}
/* footer */
.footer-wave{left:0;top:3080px;width:1200px;height:375px}
.footer-brand{left:143px;top:3226px;font-family:"Poppins",sans-serif;font-weight:500;font-size:33px;letter-spacing:1px;color:var(--white)}
.footer-links{display:grid;grid-template-columns:200px 200px;row-gap:13px;left:145px;top:3290px;font-size:15px;color:var(--white);font-weight:600}
.footer-links span::before{content:"»";margin-right:8px}
.social-title{left:905px;top:3290px;font-family:"Poppins",sans-serif;font-weight:500;font-size:20px;color:var(--white)}
.social-dots{left:907px;top:3326px;display:flex;gap:18px}
.social-dots span{width:35px;height:35px;border-radius:50%;border:2px solid var(--white);display:block}
.copyright{left:0;top:3418px;width:1200px;text-align:center;font-size:13px;color:var(--white)}
</style>
</head>
<body>

<div class="abs topbar">
  <div class="abs social"><span></span><span></span><span></span><span></span><span></span><span></span></div>
  <div class="abs account">
    <span>Wishlist(0)</span><i class="sep"></i>
    <span>My Account</span><i class="sep"></i>
    <span><svg width="14" height="13" viewBox="0 0 14 13" style="vertical-align:-2px;margin-right:6px"><path d="M0 1h2.5l2 7h7l2-5.5H4" fill="none" stroke="#fff" stroke-width="1.6"/><circle cx="5.5" cy="11" r="1.3" fill="#fff"/><circle cx="10.5" cy="11" r="1.3" fill="#fff"/></svg>0 Items</span><i class="sep"></i>
    <b>$ 0.00</b>
  </div>
</div>

<div class="abs header"></div>
<div class="abs hero" role="img" aria-label="Photo of a young girl sitting against a white brick wall reading a storybook, her hair swept up like sprouting branches with leaves"></div>
<div class="abs brand-disc"><span class="name">Lumiva Books</span></div>
<nav class="abs nav"><span>HOME</span><span>VIEW CART</span><span>NEWS &amp; EVENTS</span><span>BOOK CHOICES</span><span>CONTACT US</span></nav>
<div class="abs search-pill">
  <svg width="14" height="14" viewBox="0 0 14 14"><circle cx="6" cy="6" r="4.5" fill="none" stroke="#333" stroke-width="2"/><path d="M9.5 9.5L13 13" stroke="#333" stroke-width="2"/></svg>
  Search for books
</div>

<h1 class="abs hero-title">Sprouting<br>wonder in words</h1>
<p class="abs hero-sub">Register for FREE to discover your next adventure...</p>
<div class="abs signup"><span class="abs ph">Enter Your Email Address</span><span class="abs btn">REGISTER NOW</span></div>
<div class="abs dots"><span class="on"></span><span></span><span></span><span></span></div>

<h2 class="abs section-title welcome-title">Welcome to Lumiva Books</h2>
<p class="abs welcome-lead">Sed ut perspiciatis unde omnis iste natus voluptatem accusantium doloremque laudant adium, totam rem aperiam, eaque ipsa quae abinventore veritatis doloresutes</p>
<p class="abs welcome-body">Sed ut perspiciatis unde omnis iste natus error sit voluptatem accusantium doloremque laudantium, totam rem aperiam, eaque ipsa quae ab illo inventore veritatis et quasi architecto beatae vitae dicta sunt explicabo. Nemo enim ipsam voluptatem quia voluptas sit aspernatur aut odit aut fugit, sed quia consequuntur magni dolores</p>
<div class="abs outline-btn about-btn">MORE ABOUT US</div>

<section class="abs order-band" role="img" aria-label="Soft background of pale green leaves"></section>
<svg class="abs ribbon" viewBox="0 0 306 108"><path d="M0 0H306V78L153 108L0 78Z" fill="#2f9a2a"/></svg>
<div class="abs ribbon-text">ORDER NOW</div>
<div class="abs offer-card">
  <div class="abs offer-shadow"></div>
  <div class="abs offer-book" role="img" aria-label="Illustration of an open teal fairy tales storybook"></div>
  <h3 class="abs offer-title">Children's Books<br>at 50% OFF</h3>
  <div class="abs offer-price">$ 30.00</div>
  <div class="abs qty-row">QUANTITY <div class="qty"><span>−</span><span>1</span><span>+</span></div><div class="buy-btn">BUY NOW</div></div>
  <p class="abs offer-desc">Sed ut perspiciatis unde omnis iste natus sertror sit voluptatem accusant duium doloremque laudantium, totam rem aperiam, eaque ipsa quae ab illo inventore veritatis et quasi architecto beatae vitae dicta sunt explicabo. Nemo enim ipsam voluptatem quia voluptar magni dolores.</p>
</div>

<h2 class="abs section-title shop-title">Shop Now</h2>

<div class="abs product active" style="left:145px;top:1748px">
  <div class="frame"><div class="cover-shadow"></div><div class="cover" style="background:linear-gradient(160deg,#d43a2c,#8e1f17)" role="img" aria-label="Red storybook cover"></div></div>
  <div class="name">Sed ut perspiciatis<br>unde omnisist</div><div class="price">$ 23,00</div>
  <div class="cart-btn">ADD TO CART</div>
</div>
<div class="abs product" style="left:382px;top:1748px">
  <div class="frame"><div class="cover-shadow"></div><div class="cover" style="background:linear-gradient(160deg,#3bb3b8,#1f7d83)" role="img" aria-label="Teal storybook cover"></div></div>
  <div class="name">Sed ut perspiciatis<br>unde omnisist</div><div class="price">$ 23,00</div>
</div>
<div class="abs product" style="left:617px;top:1748px">
  <div class="frame"><div class="cover-shadow"></div><div class="cover" style="background:linear-gradient(160deg,#5dbb7a,#2f8a50)" role="img" aria-label="Green story time book cover"></div></div>
  <div class="name">Sed ut perspiciatis<br>unde omnisist</div><div class="price">$ 23,00</div>
</div>
<div class="abs product" style="left:854px;top:1748px">
  <div class="frame"><div class="cover-shadow"></div><div class="cover" style="background:linear-gradient(160deg,#f0902a,#c15f12)" role="img" aria-label="Orange storybook cover"></div></div>
  <div class="name">Sed ut perspiciatis<br>unde omnisist</div><div class="price">$ 23,00</div>
</div>

<div class="abs product" style="left:145px;top:2140px">
  <div class="frame"><div class="cover-shadow"></div><div class="cover" style="background:linear-gradient(160deg,#f3d63a,#c9a313)" role="img" aria-label="Yellow sailing storybook cover"></div></div>
  <div class="name">Sed ut perspiciatis<br>unde omnisist</div><div class="price">$ 23,00</div>
</div>
<div class="abs product" style="left:382px;top:2140px">
  <div class="frame"><div class="cover-shadow"></div><div class="cover" style="background:linear-gradient(160deg,#e6609a,#b23470)" role="img" aria-label="Pink storybook cover"></div></div>
  <div class="name">Sed ut perspiciatis<br>unde omnisist</div><div class="price">$ 23,00</div>
</div>
<div class="abs product" style="left:617px;top:2140px">
  <div class="frame"><div class="cover-shadow"></div><div class="cover" style="background:linear-gradient(160deg,#3d6fd1,#213f92)" role="img" aria-label="Blue wonderland storybook cover"></div></div>
  <div class="name">Sed ut perspiciatis<br>unde omnisist</div><div class="price">$ 23,00</div>
</div>
<div class="abs product" style="left:854px;top:2140px">
  <div class="frame"><div class="cover-shadow"></div><div class="cover" style="background:linear-gradient(160deg,#8ccc3a,#4f9420)" role="img" aria-label="Lime green adventure storybook cover"></div></div>
  <div class="name">Sed ut perspiciatis<br>unde omnisist</div><div class="price">$ 23,00</div>
</div>

<svg class="abs cursor" width="30" height="40" viewBox="0 0 30 40"><path d="M9 3a2.5 2.5 0 0 1 5 0v13l2-1a2.3 2.3 0 0 1 3 1l1 .5a2.3 2.3 0 0 1 3 1.2l1 .3a2.3 2.3 0 0 1 3 2V30c0 4-3 8-8 8h-4c-3 0-5-2-7-5L2 24a2.4 2.4 0 0 1 3.5-3L9 24Z" fill="#fff" stroke="#222" stroke-width="1.6"/></svg>

<div class="abs outline-btn more-btn">VIEW MORE</div>

<section class="abs finder"></section>
<h2 class="abs finder-title">Search for Books</h2>
<div class="abs finder-label" style="top:2716px">1. Select Child's gender</div>
<div class="abs field" style="top:2754px">Choose One <svg width="10" height="6" viewBox="0 0 10 6"><path d="M1 1l4 4 4-4" fill="none" stroke="#555" stroke-width="1.4"/></svg></div>
<div class="abs finder-label" style="top:2825px">2. Enter Child's First Name</div>
<div class="abs field" style="top:2860px">Enter Name</div>
<div class="abs finder-label" style="top:2931px">3. Enter the type of Book</div>
<div class="abs field" style="top:2971px">Choose One <svg width="10" height="6" viewBox="0 0 10 6"><path d="M1 1l4 4 4-4" fill="none" stroke="#555" stroke-width="1.4"/></svg></div>
<div class="abs search-btn">SEARCH NOW</div>
<div class="abs finder-brand">Lumiva<br>Books</div>

<svg class="abs footer-wave" viewBox="0 0 1200 375" preserveAspectRatio="none">
  <path d="M0 40C180 0 320 10 520 40S860 70 1000 35 1150 15 1200 30V375H0Z" fill="#6cbb52"/>
  <path d="M0 60C200 20 340 35 540 60S880 85 1020 55 1160 40 1200 50V375H0Z" fill="#3b9d2d"/>
</svg>
<div class="abs footer-brand">LUMIVA BOOKS</div>
<div class="abs footer-links">
  <span>HOME</span><span>SHIPPING DETAILS</span>
  <span>WHY US</span><span>BOOK CHOICES</span>
  <span>NEWS &amp; EVENTS</span><span>CONTACT US</span>
</div>
<div class="abs social-title">Lets Get Social</div>
<div class="abs social-dots"><span></span><span></span><span></span></div>
<div class="abs copyright">Copyrights © 2019 . All Rights Reserved.</div>

</body>
</html>
```